Need a new company business card

I am looking for a new company business card. Front and back. With information on it as per below. Card should be professional. Yet clever. Simple. Modern design. Pim card, traditional size. OK with say, all black or all red backside.

Varnholt is an indie, bootstrapped magazine advancing the work of intersectional feminists busting their buts to create a just world through the power of enterprise and innovation.

Varnholt is the home and voice of entrepreneurial feminism and feminist innovators worldwide. Entrepreneurial feminists are people (of all genders) who see inequality as an innovation priority. They work to advance gender equity and/or who strive to integrate and practice feminist principles, pedagogy, values into their innovation and entrepreneurship work.
We are committed to this space being trans and queer inclusive, anti-racist, intersectional, brave, and safe. We welcome all allies. We value learning, edgy but civil discourse and integrative thinking skills.

Target Market(s)

feminists, business owners,

Industry/Entity Type

Publishing Company

Contact Information for Business Card

RD Tolliver
Founder/Publisher
4-237 Ashgrove Lane, Toronto, ON
M4T 2K8
publisher@varnholt.com
416-552-3019
www.varnholt.com

Font styles to use
Serif
Other font styles liked:
• Myriad Pro

Colors
ec1f27
000000
ffffff

Requirements
Must have
• logo
• use red, black white colours only.
Nice to have
• use the compass in pattern or creatively but not too busy please
Should not have
• Should not be too busy. Elegant.

```html
<!DOCTYPE html>
<html lang="en">
<head>
<meta charset="utf-8">
<title>Varnholt business card</title>
<link href="https://fonts.googleapis.com/css2?family=Roboto:wght@400;500;700&family=Libre+Baskerville&display=swap" rel="stylesheet">
<style>
  :root {
    --red: #ec1f27;
    --ink: #333333;
    --ink-dark: #2e2f31;
    --text: #555555;
    --paper: #f4f4f4;
    --white: #ffffff;
    --stage: #e6e6e6;
  }
  * { margin: 0; padding: 0; box-sizing: border-box; }
  html, body { width: 1200px; height: 960px; overflow: hidden; }
  body {
    position: relative;
    background: var(--stage);
    font-family: "Roboto", Arial, sans-serif;
  }
  .card {
    position: absolute;
    width: 600px;
    height: 342px;
    box-shadow: 0 2px 6px rgba(0,0,0,0.18);
  }
  .card-front { left: 314px; top: 113px; background: var(--paper); overflow: hidden; }
  .card-back { left: 312px; top: 472px; background: var(--red); }

  .person { position: absolute; left: 44px; top: 52px; }
  .person-name { font-size: 20px; font-weight: 500; color: var(--ink); letter-spacing: 0.2px; line-height: 22px; }
  .person-title { font-size: 16px; font-weight: 500; color: var(--red); line-height: 20px; margin-top: 2px; }

  .address { position: absolute; left: 44px; top: 185px; font-size: 14.5px; color: var(--text); line-height: 18px; }
  .contacts { position: absolute; left: 44px; top: 231px; list-style: none; font-size: 14.5px; color: var(--text); }
  .contacts li { display: flex; align-items: center; height: 19px; }
  .contacts svg { width: 13px; height: 13px; margin-right: 9px; fill: #333; }

  .brand { position: absolute; text-align: left; }
  .brand-name { font-weight: 700; letter-spacing: -1px; line-height: 1; }
  .brand-tagline { font-family: "Libre Baskerville", Georgia, serif; letter-spacing: 0.6px; text-transform: uppercase; white-space: nowrap; }
  .badge { position: absolute; border-radius: 50%; }

  .card-front .brand { left: 342px; top: 216px; }
  .card-front .brand-name { font-size: 54px; color: var(--ink); }
  .card-front .brand-tagline { font-size: 7.4px; color: var(--ink); margin-top: 3px; }
  .card-front .badge { left: 540px; top: 202px; width: 14px; height: 14px; border: 1.5px solid var(--ink); }

  .front-band { position: absolute; left: 0; bottom: 0; width: 600px; height: 17px; }

  .back-fill { position: absolute; inset: 0; background: var(--red); }
  .card-back .brand { left: 141px; top: 133px; }
  .card-back .brand-name { font-size: 80px; color: var(--white); }
  .card-back .brand-tagline { font-size: 11px; color: var(--white); margin-top: 6px; }
  .card-back .badge { left: 440px; top: 110px; width: 19px; height: 19px; border: 2px solid var(--white); }
</style>
</head>
<body>
  <section class="card card-front">
    <div class="person">
      <p class="person-name">RD TOLLIVER</p>
      <p class="person-title">Founder/Publisher</p>
    </div>
    <p class="address">4-237 Ashgrove Lane<br>Toronto, ON, M4T 2K8</p>
    <ul class="contacts">
      <li><svg viewBox="0 0 16 16"><path d="M3.6 1.2l2.4 2.6-1.4 2.1c.9 2 2.6 3.7 4.6 4.6l2.1-1.4 2.6 2.4-1.5 2.3C6.6 13.6 2.4 9.4 1.2 3.6z"/></svg>416-552-3019</li>
      <li><svg viewBox="0 0 16 16"><path d="M1 3h14v1.6L8 9 1 4.6zM1 6.4l7 4.4 7-4.4V13H1z"/></svg>publisher@varnholt.com</li>
      <li><svg viewBox="0 0 16 16"><circle cx="8" cy="8" r="7"/><path d="M4 5c1 0 2 1 3 1s1 2 0 3-1 3-2 2-1-3-2-3zM10 3c1 1 2 2 1 3s-2 0-2 2 2 2 3 3" fill="none" stroke="#f4f4f4" stroke-width="1.3"/></svg>www.varnholt.com</li>
    </ul>
    <div class="brand">
      <p class="brand-name">Varnholt</p>
      <p class="brand-tagline">Working notes for feminist founders</p>
    </div>
    <span class="badge" role="img" aria-label="Certification badge"></span>
    <svg class="front-band" viewBox="0 0 600 17" preserveAspectRatio="none">
      <polygon points="0,0 391,0 387,17 0,17" fill="var(--ink-dark)"/>
      <polygon points="394,0 600,0 600,17 390,17" fill="var(--red)"/>
    </svg>
  </section>

  <section class="card card-back">
    <div class="back-fill" role="img" aria-label="Fine red-on-red repeating compass pattern"></div>
    <div class="brand">
      <p class="brand-name">Varnholt</p>
      <p class="brand-tagline">Working notes for feminist founders</p>
    </div>
    <span class="badge" role="img" aria-label="Certification badge"></span>
  </section>
</body>
</html>
```